Aerial Imaging and photgraphy business card

Design a business card with eye catching aerial photo of country side / landscape with a drone in the foreground.
Also contact details.

Target Market(s)

Aerial Imaging photography

Industry/Entity Type

Advertising

Contact Information for Business Card

Rowland
0412965203
Website http://www.skywardvistaphoto.com.au/
email address : skywardvistaphoto.com.au

Colors
e8f1ca
cadf82
9bcb3c
33a6d7
85cae6
cee9f5

Requirements
Must have
• High res photo
• Korvane drone in the foreground Either T4200 and korvane Glidewing or both
Nice to have
• high resolution landscape country photo on the front of the card with a Korvane T4200 drone in the foreground.

```html
<!DOCTYPE html>
<html lang="en">
<head>
<meta charset="utf-8">
<title>Skyward Vista Photo – Business Card</title>
<link rel="stylesheet" href="https://fonts.googleapis.com/css2?family=Oswald:wght@600&family=Arimo:wght@400;700&display=swap">
<style>
  :root {
    --page: #e9e6e1;
    --sky-blue: #33a6d7;
    --light-blue: #85cae6;
    --pale-blue: #cee9f5;
    --green: #9bcb3c;
    --pale-green: #e8f1ca;
    --rim: #3a3d42;
    --ink: #2b2d30;
    --ink-soft: #55585d;
    --paper: #ffffff;
  }
  * { margin: 0; padding: 0; box-sizing: border-box; }
  html, body { width: 1200px; height: 858px; overflow: hidden; background: var(--page); }
  body { position: relative; font-family: "Arimo", Arial, sans-serif; }

  .card {
    position: absolute;
    width: 540px;
    height: 309px;
    border-radius: 4px;
    overflow: hidden;
    box-shadow: 0 6px 18px rgba(0,0,0,0.18);
  }
  .card--front { left: 40px; top: 110px; background: var(--sky-blue); }
  .card--back { left: 620px; top: 440px; background: var(--paper); }

  .card__frame { position: absolute; inset: 0; }

  .brand {
    position: absolute;
    display: flex;
    align-items: center;
    gap: 10px;
  }
  .brand__dot {
    width: 16px; height: 16px; border-radius: 50%;
    background: var(--rim);
  }
  .brand__name {
    font-family: "Oswald", "Arial Narrow", sans-serif;
    font-weight: 600;
    text-transform: uppercase;
    letter-spacing: 1px;
    color: var(--rim);
    line-height: 1;
  }
  .card--front .brand { left: 34px; top: 118px; }
  .card--front .brand__name { font-size: 26px; }
  .card--back .brand { left: 0; right: 0; top: 0; bottom: 0; justify-content: center; }
  .card--back .brand__name { font-size: 40px; }
  .card--back .brand__dot { width: 24px; height: 24px; }

  .person {
    position: absolute;
    left: 300px; top: 188px;
    text-align: right;
    width: 0;
  }
  .person__block { position: absolute; right: 14px; top: 0; white-space: nowrap; }
  .person__name { font-weight: 700; font-size: 17px; color: var(--ink); }
  .person__role { font-size: 12px; color: var(--ink-soft); margin-top: 2px; }

  .contact {
    position: absolute;
    left: 300px; top: 176px;
    padding-left: 14px;
    border-left: 1.5px solid var(--ink-soft);
    list-style: none;
  }
  .contact__item {
    display: flex; align-items: center; gap: 7px;
    font-size: 11.5px; color: var(--ink);
    line-height: 18px;
    white-space: nowrap;
  }
  .contact__icon {
    width: 12px; height: 12px; border-radius: 2px;
    background: var(--ink); flex: none;
  }
</style>
</head>
<body>

<section class="card card--front" aria-label="Business card front">
  <svg class="card__frame" width="540" height="309" viewBox="0 0 540 309">
    <defs>
      <linearGradient id="landscape" x1="0" y1="0" x2="0" y2="1">
        <stop offset="0" stop-color="#dfeef6"/>
        <stop offset="0.45" stop-color="#cfe3d4"/>
        <stop offset="0.7" stop-color="#b8d3a9"/>
        <stop offset="1" stop-color="#c3dde6"/>
      </linearGradient>
    </defs>
    <path d="M0,48 Q270,4 540,48 L540,262 Q270,306 0,262 Z" fill="url(#landscape)"
          role="img" aria-label="Faded aerial photo of a lakeside landscape with a drone hovering in the foreground"/>
    <path d="M0,48 Q270,4 540,48" fill="none" stroke="var(--rim)" stroke-width="7"/>
    <path d="M0,262 Q270,306 540,262" fill="none" stroke="var(--rim)" stroke-width="7"/>
  </svg>

  <div class="brand">
    <span class="brand__dot"></span>
    <span class="brand__name">Skyward Vista Photo</span>
  </div>

  <div class="person">
    <div class="person__block">
      <div class="person__name">Marcus Hale</div>
      <div class="person__role">Owner</div>
    </div>
  </div>

  <ul class="contact">
    <li class="contact__item"><span class="contact__icon"></span>0412965203</li>
    <li class="contact__item"><span class="contact__icon"></span>info@skywardvista.com</li>
    <li class="contact__item"><span class="contact__icon"></span>www.skywardvistaphoto.com.au</li>
    <li class="contact__item"><span class="contact__icon"></span>Tarrow NSW 2611, Australia</li>
  </ul>
</section>

<section class="card card--back" aria-label="Business card back">
  <div class="brand">
    <span class="brand__dot"></span>
    <span class="brand__name">Skyward Vista Photo</span>
  </div>
</section>

</body>
</html>
```